Business Name: DM Space Arranging Pty Ltd

Business Type: Professional Home Styling and Minor Renovation Business

Logo: Attached is the logo that has been created.
I always envisaged the logo in the middle of the business card with my full name underneath it.

Marnie Tulloch B.Com LMR HTV
Property Stylist & Project Manager

Include dot points of services
Staging Houses for Sale
Minor Home Renovations
Home Styling & Project Management
Re-Designing Living Spaces to Aid the Disabled

Somewhere on the card I would like to incorporate
"Property Styling and Cosmetic Renovations"

Colour Scheme:
Gloss black business card, with white and then
Gold or Silver as the highlight colours.

Incorporate a small amount of yellow only if possible to make it pop. If this really doesn’t work it doesn’t have to be used. Also l like the colour teal if that needs to be used as a contrast colour.

Feel/Themes
• I love antique chairs, regal expensive looking furniture mixed with modern homes (this is the unique style I want to sell) antique and modern mix that looks high class as well as modern and fresh, targeting an executive market.
• I want to use an orchid as a trademark throughout the course of my work, not sure if this can somehow be incorporated? Also really like crowns to give that regal/antique feel and then something else to give that modern twist (I don’t know what the something else could be)
• Wall Paper Look (on a portion of it not all of it, like a French look)
• Overall feel - A very deluxe and professional feel with a little bit of creative flare.

I hope this helps create a bit of a picture.

Is it ok that I call you tomorrow morning? My mobile number is 0438 926 574 if you have any questions for me in the meantime.

Target Market(s)

High Quality Executive Market - People selling homes

Industry/Entity Type

Business

Contact Information for Business Card

Include dot points of services:
Staging Houses for Sale
Minor Home Renovations

Font styles to use
Serif
Script

Colors
33b8a4
fbed22

Requirements
Must have
• Marnie Tulloch B.Com LMR HTV
• Property Stylist & Project Manager
• LMR and HTV Logos on the card
• "Dramatically increase the value of your property"
Nice to have
• Colour Scheme:
• Gloss black business card, with white and then
• Gold or Silver as the highlight colours.
• Incorporate a small amount of yellow only if possible to make it pop. If this really doesn’t work it doesn’t have to be used. Also l like the colour teal if that needs to be used as a contrast colour.
• Also like teal as a highlight colour.

```html
<!DOCTYPE html>
<html lang="en">
<head>
<meta charset="utf-8">
<title>DM Space Arranging Pty Ltd – Business Card</title>
<link rel="stylesheet" href="https://fonts.googleapis.com/css2?family=Great+Vibes&family=Old+Standard+TT:wght@400&display=swap">
<style>
  :root {
    --backdrop: #1d1d1f;
    --card-white: #ffffff;
    --ink: #2a2a2a;
    --logo-grey: #6f6f6f;
    --gloss-black: #0b0b0b;
    --gold-light: #f3d27a;
    --gold-mid: #c9a13b;
    --gold-dark: #8a6a1e;
    --teal: #33b8a4;
  }
  * { box-sizing: border-box; margin: 0; padding: 0; }
  html, body {
    width: 1200px;
    height: 852px;
    overflow: hidden;
    background: var(--backdrop);
  }
  .stage {
    position: relative;
    width: 1200px;
    height: 852px;
  }
  .card {
    position: absolute;
    top: 281px;
    width: 500px;
    height: 290px;
    border-radius: 14px;
    background: var(--card-white);
    overflow: hidden;
    box-shadow: 0 18px 40px rgba(0,0,0,.55);
  }
  .card--front { left: 60px; }
  .card--back  { left: 640px; }

  .card__trim {
    position: absolute;
    inset: 0;
    width: 100%;
    height: 100%;
  }

  .wordmark {
    position: absolute;
    font-family: "Old Standard TT", Georgia, serif;
    font-weight: 400;
    color: var(--logo-grey);
    text-transform: uppercase;
    letter-spacing: .22em;
    text-align: center;
    line-height: 1.5;
  }
  .card--front .wordmark {
    left: 0; right: 0;
    top: 112px;
    font-size: 17px;
  }
  .card--back .wordmark {
    left: 255px;
    width: 225px;
    top: 38px;
    font-size: 11px;
  }

  .back__band {
    position: absolute;
    left: 0; top: 0; bottom: 0;
    width: 74px;
  }

  .holder {
    position: absolute;
    left: 98px;
    top: 34px;
  }
  .holder__name {
    font-family: "Great Vibes", cursive;
    font-size: 31px;
    color: var(--ink);
    line-height: 1.1;
    margin-bottom: 8px;
  }
  .holder__title {
    font-family: "Old Standard TT", Georgia, serif;
    font-size: 13px;
    color: var(--ink);
    line-height: 1.25;
  }

  .tagline {
    position: absolute;
    left: 262px;
    top: 118px;
    width: 210px;
    font-family: "Old Standard TT", Georgia, serif;
    font-size: 11.5px;
    color: var(--ink);
    text-align: center;
  }

  .services {
    position: absolute;
    left: 100px;
    top: 178px;
    list-style: none;
    font-family: "Old Standard TT", Georgia, serif;
    font-size: 13.5px;
    color: var(--ink);
    line-height: 1.55;
  }
  .services li::before {
    content: "»";
    color: var(--teal);
    margin-right: 9px;
  }
</style>
</head>
<body>
<main class="stage">

  <section class="card card--front" aria-label="Card front">
    <svg class="card__trim" viewBox="0 0 500 290" preserveAspectRatio="none" aria-hidden="true">
      <defs>
        <linearGradient id="goldFront" x1="0" y1="0" x2="1" y2="0">
          <stop offset="0" stop-color="var(--gold-dark)"/>
          <stop offset=".45" stop-color="var(--gold-light)"/>
          <stop offset="1" stop-color="var(--gold-mid)"/>
        </linearGradient>
      </defs>
      <polygon points="0,258 500,196 500,206 0,270" fill="url(#goldFront)"/>
      <polygon points="0,270 170,249 95,290 0,290" fill="var(--gloss-black)"/>
    </svg>
    <p class="wordmark">DM Space Arranging<br>Pty Ltd</p>
  </section>

  <section class="card card--back" aria-label="Card back">
    <svg class="back__band" viewBox="0 0 74 290" preserveAspectRatio="none" aria-hidden="true">
      <defs>
        <linearGradient id="goldEdge" x1="0" y1="0" x2="0" y2="1">
          <stop offset="0" stop-color="var(--gold-light)"/>
          <stop offset=".5" stop-color="var(--gold-mid)"/>
          <stop offset="1" stop-color="var(--gold-dark)"/>
        </linearGradient>
      </defs>
      <rect x="0" y="0" width="68" height="290" fill="var(--gloss-black)"/>
      <rect x="68" y="0" width="6" height="290" fill="url(#goldEdge)"/>
    </svg>

    <div class="holder">
      <h1 class="holder__name">Marnie Tulloch</h1>
      <p class="holder__title">B.Com LMR HTV<br>Property Stylist &amp;<br>Project Manager</p>
    </div>

    <p class="wordmark">DM Space Arranging<br>Pty Ltd</p>
    <p class="tagline">Property Styling &amp; Cosmetic Renovations</p>

    <ul class="services">
      <li>Staging Houses for Sale</li>
      <li>Minor Home Renovations</li>
      <li>Home Styling &amp; Project Management</li>
      <li>Re-Designing Living Spaces to Aid the Disabled</li>
    </ul>
  </section>

</main>
</body>
</html>
```